Real Estate Card Design

I need a new business card! Below you will find my headshot, the company logo and a copy of my previous business card.

The card must contain the following information:

Dana Wexley
Sales Representative
LARKMERE REALTY INC BROKERGE
204-517 Marsh Rd E, Oshawa ON L1H 4K7
Cell: 905-618-3074 Office:905-481-2696
www.danawexley.example dana@homesbywexley.example

I would like the card to portray security and class all the while being fresh and contemporary. I hold the key....

```html
<!DOCTYPE html>
<html lang="en">
<head>
<meta charset="utf-8">
<title>Dana Wexley – Business Card</title>
<link href="https://fonts.googleapis.com/css2?family=Crimson+Pro:wght@400;600;700&display=swap" rel="stylesheet">
<style>
  :root {
    --page: #e6e7e9;
    --card: #ffffff;
    --brand-blue: #0f9ee3;
    --ink: #141414;
    --photo-top: #5c5d60;
    --photo-bottom: #2a2c31;
  }
  * { box-sizing: border-box; margin: 0; padding: 0; }
  html, body {
    width: 1200px; height: 1000px; overflow: hidden;
    background: var(--page);
    font-family: "Crimson Pro", Georgia, serif;
    color: var(--ink);
  }
  .stage { position: relative; width: 1200px; height: 1000px; }
  .card {
    position: absolute; left: 250px;
    width: 700px; height: 400px;
    background: var(--card);
    border-radius: 22px;
    overflow: hidden;
    box-shadow: 0 6px 18px rgba(0,0,0,.12);
  }
  .card--back { top: 70px; }
  .card--front { top: 530px; }

  /* company name: one colour, one weight, one size */
  .company {
    display: flex; align-items: center; gap: 14px;
  }
  .company__dot {
    flex: none; border-radius: 50%; background: var(--brand-blue);
  }
  .company__name {
    font-weight: 700; color: var(--ink);
    text-transform: uppercase; line-height: 1.1;
    letter-spacing: 1px;
  }

  .card--back .company {
    position: absolute; left: 0; right: 0; top: 178px;
    justify-content: center;
  }
  .card--back .company__dot { width: 26px; height: 26px; }
  .card--back .company__name { font-size: 32px; }
  .back-band {
    position: absolute; left: 0; right: 0; bottom: 0;
    height: 34px; background: var(--brand-blue);
  }

  /* front */
  .info {
    position: absolute; left: 0; top: 0; bottom: 0; width: 380px;
    padding: 44px 0 0 38px;
  }
  .card--front .company__dot { width: 16px; height: 16px; }
  .card--front .company__name { font-size: 22px; }
  .brand-rule {
    margin-top: 14px; width: 300px; height: 2px; background: var(--brand-blue);
  }
  .agent-name {
    margin-top: 18px;
    font-size: 27px; font-weight: 600; color: var(--brand-blue);
    letter-spacing: 1px; text-transform: uppercase; line-height: 1;
  }
  .agent-role { font-size: 18px; margin-top: 2px; }
  .address { margin-top: 14px; font-size: 16px; font-weight: 600; }
  .phones { margin-top: 8px; font-size: 17px; font-weight: 600; line-height: 1.2; }
  .phones .label { color: var(--brand-blue); }
  .links { margin-top: 10px; font-size: 16px; font-weight: 600; line-height: 1.45; }
  .links li { list-style: none; display: flex; align-items: center; gap: 8px; }
  .links svg { width: 16px; height: 16px; flex: none; }

  .photo {
    position: absolute; right: 0; top: 0; bottom: 0; width: 320px;
    background: linear-gradient(180deg, var(--photo-top) 0%, #4b4c50 55%, var(--photo-bottom) 100%);
  }
</style>
</head>
<body>
<main class="stage">

  <section class="card card--back" aria-label="Card back">
    <div class="company">
      <span class="company__dot"></span>
      <p class="company__name">Larkmere Realty Inc Brokerge</p>
    </div>
    <div class="back-band"></div>
  </section>

  <section class="card card--front" aria-label="Card front">
    <div class="info">
      <div class="company">
        <span class="company__dot"></span>
        <p class="company__name">Larkmere Realty<br>Inc Brokerge</p>
      </div>
      <div class="brand-rule"></div>

      <h1 class="agent-name">Dana Wexley</h1>
      <p class="agent-role">Sales Representative</p>

      <p class="address">204-517 Marsh Rd E, Oshawa ON L1H 4K7</p>

      <p class="phones">
        <span class="label">Cell:</span> 905-618-3074<br>
        <span class="label">Office:</span> 905-481-2696
      </p>

      <ul class="links">
        <li>
          <svg viewBox="0 0 16 16" aria-hidden="true"><rect x="1" y="3" width="14" height="10" rx="1.5" fill="var(--brand-blue)"/><path d="M1.5 4 8 9l6.5-5" stroke="#fff" stroke-width="1.3" fill="none"/></svg>
          dana@homesbywexley.example
        </li>
        <li>
          <svg viewBox="0 0 16 16" aria-hidden="true"><circle cx="8" cy="8" r="6.5" fill="none" stroke="var(--brand-blue)" stroke-width="1.4"/><ellipse cx="8" cy="8" rx="2.8" ry="6.5" fill="none" stroke="var(--brand-blue)" stroke-width="1.2"/><path d="M1.5 8h13" stroke="var(--brand-blue)" stroke-width="1.2"/></svg>
          www.danawexley.example
        </li>
      </ul>
    </div>

    <div class="photo" role="img" aria-label="Portrait of the agent in a pinstripe suit, holding up a house key"></div>
  </section>

</main>
</body>
</html>
```